New PowerPoint Design Project

I need a company powerpoint template for my company, Varnok (see design file logo attached), that has a number of templated slides with an exciting supporting colour palette. Needs to have header and footer sections, tables in colour which support the logo colour, bar and line charts, dot point slides and image (placeholders) slides. Logo is attached.
The primary use of this template is to pitch for new work - ie about us page, previous clients page, then a breakdown of services offered in a table format with prices etc...
Updates

Hi everyone
Please see some example PPT templates that provide more of a guide as to what I need.

Thanks
Leopold

Font styles to use
Serif
Sans Serif

Colors
0054AA
0677BA
7BADD7
CADEEF
E8F1F8
00AB8E
00BBA5
67D7C9
C6EFE9
E9F9F6
59FF00
82FF00
B8FF75
E3FFCB
F4FFEA
FFC000
F8CF3A
FAE287
FDF2CF
FEFAEE

```html
<!DOCTYPE html>
<html lang="en">
<head>
<meta charset="utf-8">
<title>Varnok Presentation Template</title>
<link rel="stylesheet" href="https://fonts.googleapis.com/css2?family=Marcellus&family=Cormorant+Garamond:ital,wght@0,400;1,400&family=Jost:wght@300;400;500&display=swap">
<style>
:root{
  --canvas:#e4e6e5;
  --pine:#0b3a2f;
  --pine-deep:#062a21;
  --forest:#1f5a3f;
  --navy:#121d25;
  --gold:#d9a62b;
  --gold-soft:#e9c35a;
  --neon:#2bd14a;
  --mint:#8fd59a;
  --leaf:#3c8a5a;
  --paper:#ffffff;
  --ink:#26332e;
  --muted:#8a958f;
  --serif:"Marcellus",serif;
  --italic:"Cormorant Garamond",serif;
  --sans:"Jost",sans-serif;
}
*{box-sizing:border-box;margin:0;padding:0}
html,body{width:667px;height:1200px;overflow:hidden}
body{background:var(--canvas);display:flex;align-items:center;justify-content:center;font-family:var(--sans);font-weight:300;color:var(--ink)}
h1,h2,h3,b,strong{font-weight:400}
.deck{display:grid;grid-template-columns:repeat(3,213px);grid-auto-rows:120px;gap:5px}
.slide{position:relative;overflow:hidden;background:var(--paper)}
.bar{position:absolute;top:0;left:0;right:0;height:13px;background:var(--pine);display:flex;align-items:center;justify-content:space-between;padding:0 6px;z-index:2}
.bar .brand{font-family:var(--serif);font-weight:400;font-size:5px;color:var(--gold);letter-spacing:.3px}
.bar .legal{font-size:2.4px;color:var(--gold);opacity:.7}
.bar .dot{width:5px;height:5px;border-radius:50%;background:var(--gold)}
.footnote{position:absolute;bottom:3px;left:0;right:0;text-align:center;font-size:2.2px;color:var(--muted)}
.dark .footnote{color:#c9d6cf}
.title{font-family:var(--serif);font-weight:400;font-size:7px;line-height:1.25;color:var(--ink);letter-spacing:.1px}
.title i{font-family:var(--italic);font-style:italic;font-weight:400;font-size:7.6px}
.dark .title{color:#fff}
.fine{font-size:2.2px;line-height:1.5;color:var(--muted)}
.dark .fine{color:#cfdcd5}
.ph{position:absolute;border-radius:5px}
.ph-car{background:radial-gradient(ellipse at 55% 60%,#2fc24c 0%,#0f4a22 35%,#050b08 75%)}
.ph-car2{background:linear-gradient(135deg,#0a0f0c 30%,#1c7a33 65%,#47e05a)}
.ph-face{background:linear-gradient(160deg,#d9d2c9,#b99a78 55%,#6e5a49)}
.ph-person{background:linear-gradient(180deg,#eef0f1,#b8a89a 55%,#4c6a8c)}

/* 1 title */
.s-cover{background:radial-gradient(ellipse at 25% 75%,#1d5a34 0%,transparent 55%),linear-gradient(120deg,#0c2a1c 0%,#0a2418 45%,#05140e 100%)}
.s-cover .word{position:absolute;top:42px;width:100%;text-align:center;font-family:var(--serif);font-weight:400;font-size:24px;color:var(--gold);letter-spacing:1px}
.s-cover .sub{position:absolute;top:72px;width:100%;text-align:center;font-family:var(--serif);font-weight:400;font-size:5.5px;color:var(--gold-soft)}

/* 2 hero */
.s-hero{background:var(--pine)}
.s-hero .ph{left:4px;top:17px;right:4px;bottom:4px;border-radius:6px}
.s-hero .headline{position:absolute;left:12px;top:82px;font-family:var(--serif);font-weight:400;font-size:7.5px;color:#fff;line-height:1.2}
.s-hero .headline mark{background:var(--leaf);color:#fff;padding:0 3px;border-radius:1px}
.s-hero .note{position:absolute;left:150px;top:86px;width:54px;font-size:2px;color:#e0ece5;line-height:1.5}
.pill{position:absolute;font-size:2.6px;color:#fff;background:var(--leaf);border-radius:4px;padding:1.5px 6px}
.circ{position:absolute;width:6px;height:6px;border-radius:50%;border:.6px solid var(--neon)}

/* 3 decisions */
.s-navy{background:var(--navy)}
.card{position:absolute;border-radius:4px}
.card-line{border:.5px solid #3b4a52}
.card-green{background:linear-gradient(160deg,#2e7a4d,#9fd4a9)}
.chip{position:absolute;width:5px;height:5px;border-radius:50%;background:#e6efe9;opacity:.8}
.card .cap{position:absolute;left:4px;font-size:2.6px;color:#fff;line-height:1.3}
.arrow-ne{position:absolute;right:3px;top:2px;font-size:3px;color:#fff}
.nav-dot{position:absolute;width:5px;height:5px;border-radius:50%;background:var(--neon);color:#062a21;font-size:3.4px;line-height:5px;text-align:center}

/* 4 team */
.s-team{background:linear-gradient(180deg,var(--pine) 75%,transparent 75%),linear-gradient(90deg,#1f5a3f,#f0f3f1)}
.member{position:absolute;top:38px;width:34px;height:49px;background:#fff;border-radius:2px}
.member .ph{left:0;right:0;top:0;height:31px;border-radius:2px 2px 0 0}
.member .name{position:absolute;top:34px;width:100%;text-align:center;font-family:var(--serif);font-size:2.8px;color:var(--ink)}
.member .role{position:absolute;top:39px;width:100%;text-align:center;font-size:2px;color:var(--muted)}

/* 5 profile */
.s-profile{background:linear-gradient(160deg,#2f7352,#0f3f31)}
.s-profile .ph{left:0;top:0;width:97px;height:120px;border-radius:0}
.meter{position:absolute;left:114px;width:82px}
.meter .lbl{font-size:2px;color:#e5efe9;display:flex;justify-content:space-between;align-items:flex-end}
.meter .lbl .pct{font-family:var(--serif);font-size:3.4px}
.meter .track{height:1.8px;background:rgba(255,255,255,.25);margin-top:1px}
.meter .fill{height:100%;width:90%;background:#fff}

/* 6 services */
.s-services{background:linear-gradient(180deg,transparent 44%,var(--pine) 44%),linear-gradient(90deg,var(--forest),#eef2ef)}
.svc{position:absolute;width:51px;height:16px;background:#fff;border-radius:2px;padding:2px 3px 0 9px}
.svc .tag{position:absolute;left:-2px;top:5px;width:5px;height:5px;border-radius:50%;background:var(--leaf);color:#fff;font-size:2.4px;line-height:5px;text-align:center}
.svc .t{font-family:var(--serif);font-size:2.6px;color:var(--ink)}

/* 8 pricing */
.plan{position:absolute;top:30px;width:52px}
.plan .price{font-family:var(--serif);font-size:7px;color:var(--ink)}
.plan .price sup{font-size:3px}
.plan .price small{font-family:var(--sans);font-size:2px;color:var(--muted)}
.plan .tier{font-size:2.6px;color:var(--gold);margin:1px 0 2px}
.plan ul{list-style:none;margin-top:2px}
.plan li{font-size:2px;color:var(--muted);display:flex;align-items:center;gap:1.5px;margin-bottom:1.2px}
.plan li::before{content:"";width:2.4px;height:2.4px;border-radius:50%;border:.4px solid var(--leaf)}
.plan .btn{margin-top:3px;height:4.5px;border-radius:1px;background:var(--pine);color:#fff;font-size:1.9px;line-height:4.5px;padding:0 3px;width:38px;position:relative}
.plan .btn::after{content:"→";position:absolute;right:2px;color:var(--neon)}

/* 9 portfolio */
.s-portfolio{background:var(--pine)}
.grid9{position:absolute;left:9px;top:17px;right:9px;bottom:5px;display:grid;grid-template-columns:repeat(3,1fr);grid-template-rows:repeat(3,1fr);gap:2px}
.grid9 .ph{position:static;border-radius:2px}
.grid9 .center{background:linear-gradient(160deg,#6aa57f,#d7e8dc);border-radius:2px;text-align:center;padding-top:6px}
.grid9 .center .title{color:#fff}

/* 10 disruptions */
.point{position:absolute;width:36px}
.point .badge{position:absolute;left:-11px;top:0;width:5px;height:5px;border-radius:50%;background:var(--leaf);color:#fff;font-size:2.4px;line-height:5px;text-align:center}
.point .t{font-family:var(--serif);font-size:2.8px}

/* 13 infographic */
.ring{position:absolute;top:32px;width:29px;height:29px;border-radius:50%;border:3px solid}
.ring svg{position:absolute;left:50%;top:50%;transform:translate(-50%,-50%)}
.step{position:absolute;top:66px;width:34px;text-align:center}
.step .t{font-family:var(--serif);font-size:2.8px;color:var(--ink)}

/* 15 thanks */
.s-thanks{background:linear-gradient(180deg,#1f4a37 70%,#163a2b 70%)}
.s-thanks .big{position:absolute;left:11px;top:13px;font-family:var(--serif);font-weight:400;font-size:17px;line-height:1.05;color:var(--gold)}
.contact{position:absolute;bottom:6px;width:60px;text-align:center;color:#e6efe9}
.contact .k{font-size:2.6px}
.contact .v{font-size:2px;line-height:1.5;opacity:.85}
</style>
</head>
<body>
<main class="deck">

  <section class="slide s-cover">
    <h1 class="word">VARNOK</h1>
    <p class="sub">VARNOK Presentation Template</p>
  </section>

  <section class="slide s-hero">
    <header class="bar"><span class="brand">VARNOK</span><span class="legal">Copyright © Varnok. All rights reserved</span><span class="dot"></span></header>
    <div class="ph ph-car" role="img" aria-label="Photo of a dark sports car lit with green light"></div>
    <h2 class="headline">Analyzing Case Studies for<br><mark>Business Growth</mark></h2>
    <p class="note">Short summary of the growth story and the key results we reached together.</p>
    <span class="pill" style="left:150px;top:100px">Let's Talks</span>
    <span class="circ" style="left:174px;top:100px"></span>
  </section>

  <section class="slide s-navy dark">
    <header class="bar" style="background:var(--navy)"><span class="brand">VARNOK</span><span class="legal">Copyright © Varnok. All rights reserved</span><span class="dot"></span></header>
    <h2 class="title" style="position:absolute;left:12px;top:18px">Case Studies in Decision<br><i>Making Excellence</i></h2>
    <span class="nav-dot" style="left:184px;top:23px">←</span>
    <span class="nav-dot" style="left:192px;top:23px">→</span>
    <div class="ph ph-car" style="left:11px;top:45px;width:44px;height:64px" role="img" aria-label="Photo of a green-lit car"></div>
    <div class="card card-green" style="left:59px;top:45px;width:44px;height:64px">
      <span class="chip" style="left:3px;top:3px"></span><span class="arrow-ne">↗</span>
      <span class="cap" style="top:30px">Case Studies in Market<br>Success</span>
      <span class="cap fine" style="top:40px;width:38px;color:#eef7f1">Notes on the market study and the results it gave the team.</span>
    </div>
    <div class="card card-line" style="left:107px;top:45px;width:45px;height:19px">
      <span class="chip" style="left:3px;top:3px"></span><span class="arrow-ne">↗</span>
      <span class="cap" style="top:10px">Case Studies in Market<br>Success</span>
    </div>
    <div class="card card-line" style="left:107px;top:67px;width:45px;height:23px">
      <span class="chip" style="left:3px;top:3px"></span><span class="arrow-ne">↗</span>
      <span class="cap" style="top:14px">Case Studies of Technology-Driven<br>Change</span>
    </div>
    <div class="footnote">Insert your footer title here</div>
  </section>

  <section class="slide s-team dark">
    <header class="bar"><span class="brand">VARNOK</span><span class="legal">Copyright © Varnok. All rights reserved</span><span class="dot"></span></header>
    <h2 class="title" style="position:absolute;left:11px;top:18px">Case Studies of<br><i>Entrepreneurial Success</i></h2>
    <p class="fine" style="position:absolute;left:93px;top:20px;width:60px">A short line about the people who lead each project for you.</p>
    <div class="member" style="left:11px"><div class="ph ph-person" role="img" aria-label="Portrait of team member"></div><div class="name">Owen R. Hale</div><div class="role">Position here</div></div>
    <div class="member" style="left:49px"><div class="ph ph-person" role="img" aria-label="Portrait of team member"></div><div class="name">Marcus T. Reed</div><div class="role">Position here</div></div>
    <div class="member" style="left:87px"><div class="ph ph-person" role="img" aria-label="Portrait of team member"></div><div class="name">Peter J. Lund</div><div class="role">Position here</div></div>
    <div class="member" style="left:125px"><div class="ph ph-person" role="img" aria-label="Portrait of team member"></div><div class="name">Dario F. Vance</div><div class="role">Position here</div></div>
    <div class="footnote" style="color:var(--ink);width:96px">Insert your footer title here</div>
  </section>

  <section class="slide s-profile dark">
    <header class="bar" style="background:transparent;left:97px"><span class="brand">VARNOK</span><span class="legal">Copyright © Varnok. All rights reserved</span><span class="dot"></span></header>
    <div class="ph ph-face" role="img" aria-label="Portrait photo of a smiling woman"></div>
    <h2 class="title" style="position:absolute;left:114px;top:25px">Elena M. Corwin</h2>
    <div class="meter" style="top:40px"><div class="lbl"><span>Title text here</span><span class="pct">90%</span></div><div class="track"><div class="fill"></div></div></div>
    <div class="meter" style="top:53px"><div class="lbl"><span>Title text here</span><span class="pct">90%</span></div><div class="track"><div class="fill"></div></div></div>
    <div class="meter" style="top:66px"><div class="lbl"><span>Title text here</span><span class="pct">90%</span></div><div class="track"><div class="fill"></div></div></div>
    <div class="footnote" style="left:97px">Insert your footer title here</div>
  </section>

  <section class="slide s-services dark">
    <header class="bar"><span class="brand">VARNOK</span><span class="legal">Copyright © Varnok. All rights reserved</span><span class="dot"></span></header>
    <h2 class="title" style="position:absolute;left:11px;top:18px">Case Studies of<br><i>Entrepreneurial Success</i></h2>
    <p class="fine" style="position:absolute;left:128px;top:20px;width:70px;color:#fff">A short line on the services we offer and how we price them.</p>
    <div class="svc" style="left:21px;top:48px"><span class="tag">A</span><div class="t">Service One</div><div class="fine">Brief note on this service</div></div>
    <div class="svc" style="left:81px;top:48px"><span class="tag">B</span><div class="t">Service Two</div><div class="fine">Brief note on this service</div></div>
    <div class="svc" style="left:141px;top:48px"><span class="tag">C</span><div class="t">Service Three</div><div class="fine">Brief note on this service</div></div>
    <div class="svc" style="left:21px;top:76px"><span class="tag">D</span><div class="t">Service Four</div><div class="fine">Brief note on this service</div></div>
    <div class="svc" style="left:81px;top:76px"><span class="tag">E</span><div class="t">Service Five</div><div class="fine">Brief note on this service</div></div>
    <div class="svc" style="left:141px;top:76px"><span class="tag">F</span><div class="t">Service Six</div><div class="fine">Brief note on this service</div></div>
    <div class="footnote">Insert your footer title here</div>
  </section>

  <section class="slide">
    <header class="bar"><span class="brand">VARNOK</span><span class="legal">Copyright © Varnok. All rights reserved</span><span class="dot"></span></header>
    <h2 class="title" style="position:absolute;left:18px;top:32px">Case Studies of<br><i>Entrepreneurial Success</i></h2>
    <svg style="position:absolute;left:14px;top:60px" width="80" height="42" viewBox="0 0 80 42">
      <g font-size="1.8" fill="#6a7a72" font-family="Jost,sans-serif"><circle cx="4" cy="2" r=".8" fill="#3c8a5a"/><text x="5.5" y="2.6">1st Qtr</text><circle cx="12" cy="2" r=".8" fill="#92c57e"/><text x="13.5" y="2.6">2nd Qtr</text>
      <circle cx="42" cy="2" r=".8" fill="#3c8a5a"/><text x="43.5" y="2.6">1st Qtr</text><circle cx="50" cy="2" r=".8" fill="#92c57e"/><text x="51.5" y="2.6">2nd Qtr</text></g>
      <circle cx="23" cy="24" r="9" fill="none" stroke="#3c8a5a" stroke-width="4"/>
      <circle cx="23" cy="24" r="9" fill="none" stroke="#a6d88a" stroke-width="4" stroke-dasharray="16 41" transform="rotate(-160 23 24)"/>
      <circle cx="61" cy="24" r="9" fill="none" stroke="#3c8a5a" stroke-width="4"/>
      <circle cx="61" cy="24" r="9" fill="none" stroke="#a6d88a" stroke-width="4" stroke-dasharray="24 33" transform="rotate(-200 61 24)"/>
    </svg>
    <svg style="position:absolute;left:104px;top:18px" width="100" height="92" viewBox="0 0 100 92">
      <g stroke="#eef0ef" stroke-width=".4"><line x1="8" y1="6" x2="98" y2="6"/><line x1="8" y1="20" x2="98" y2="20"/><line x1="8" y1="34" x2="98" y2="34"/><line x1="8" y1="48" x2="98" y2="48"/><line x1="8" y1="62" x2="98" y2="62"/><line x1="8" y1="76" x2="98" y2="76"/></g>
      <g fill="#a0aaa5" font-size="2" font-family="Jost,sans-serif"><text x="0" y="7">500</text><text x="0" y="21">400</text><text x="0" y="35">300</text><text x="0" y="49">200</text><text x="0" y="63">100</text><text x="3" y="77">0</text>
      <text x="14" y="82">Group 1</text><text x="37" y="82">Group 2</text><text x="60" y="82">Group 3</text><text x="83" y="82">Group 4</text></g>
      <rect x="12" y="66" width="4" height="10" fill="#f2e48c"/><rect x="16" y="10" width="4" height="66" fill="#3f7a67"/><rect x="20" y="50" width="4" height="26" fill="#92c57e"/><rect x="24" y="68" width="4" height="8" fill="#d9a24c"/>
      <rect x="35" y="56" width="4" height="20" fill="#f2e48c"/><rect x="39" y="47" width="4" height="29" fill="#3f7a67"/><rect x="43" y="44" width="4" height="32" fill="#92c57e"/><rect x="47" y="46" width="4" height="30" fill="#d9a24c"/>
      <rect x="58" y="61" width="4" height="15" fill="#f2e48c"/><rect x="62" y="64" width="4" height="12" fill="#3f7a67"/><rect x="66" y="26" width="4" height="50" fill="#92c57e"/><rect x="70" y="37" width="4" height="39" fill="#d9a24c"/>
      <rect x="81" y="46" width="4" height="30" fill="#f2e48c"/><rect x="85" y="52" width="4" height="24" fill="#3f7a67"/><rect x="89" y="34" width="4" height="42" fill="#92c57e"/><rect x="93" y="39" width="4" height="37" fill="#d9a24c"/>
    </svg>
    <div class="footnote">Insert your footer title here</div>
  </section>

  <section class="slide">
    <header class="bar"><span class="brand">VARNOK</span><span class="legal">Copyright © Varnok. All rights reserved</span><span class="dot"></span></header>
    <h2 class="title" style="position:absolute;left:26px;top:24px">Pricing Plan</h2>
    <p class="fine" style="position:absolute;left:90px;top:24px;width:100px">A short note on how each package is built and what it includes for clients.</p>
    <div class="plan" style="left:26px"><div class="price"><sup>$</sup>149 <small>Semester</small></div><div class="tier">Silver Package</div><p class="fine">What this plan gives you.</p><ul><li>Core support</li><li>Weekly report</li><li>One review</li></ul><div class="btn">Get Started</div></div>
    <div class="plan" style="left:89px"><div class="price"><sup>$</sup>249 <small>Semester</small></div><div class="tier">Medium Package</div><p class="fine">What this plan gives you.</p><ul><li>Core support</li><li>Weekly report</li><li>Two reviews</li><li>Team sessions</li></ul><div class="btn">Get Started</div></div>
    <div class="plan" style="left:149px"><div class="price"><sup>$</sup>479 <small>Semester</small></div><div class="tier">Premium Package</div><p class="fine">What this plan gives you.</p><ul><li>Core support</li><li>Daily report</li><li>Four reviews</li><li>Team sessions</li><li>Full audit</li></ul><div class="btn">Get Started</div></div>
  </section>

  <section class="slide s-portfolio dark">
    <header class="bar"><span class="brand">VARNOK</span><span class="legal">Copyright © Varnok. All rights reserved</span><span class="dot"></span></header>
    <div class="grid9">
      <div class="ph ph-car" role="img" aria-label="Portfolio photo"></div>
      <div class="ph ph-car2" role="img" aria-label="Portfolio photo"></div>
      <div class="ph ph-car" role="img" aria-label="Portfolio photo"></div>
      <div class="ph ph-car2" role="img" aria-label="Portfolio photo"></div>
      <div class="center"><h2 class="title">Our Portfolio</h2><p class="fine" style="color:#fff;padding:1px 6px">A short line on the work shown in this gallery.</p></div>
      <div class="ph ph-car2" role="img" aria-label="Portfolio photo"></div>
      <div class="ph ph-car" role="img" aria-label="Portfolio photo"></div>
      <div class="ph ph-car2" role="img" aria-label="Portfolio photo"></div>
      <div class="ph ph-car" role="img" aria-label="Portfolio photo"></div>
    </div>
  </section>

  <section class="slide" style="background:linear-gradient(90deg,var(--leaf) 28%,var(--paper) 28%)">
    <header class="bar"><span class="brand">VARNOK</span><span class="legal">Copyright © Varnok. All rights reserved</span><span class="dot"></span></header>
    <div class="ph ph-car" style="left:14px;top:34px;width:30px;height:72px;border-radius:3px" role="img" aria-label="Photo of a green-lit car"></div>
    <div class="ph ph-car" style="left:32px;top:17px;width:46px;height:100px;border-radius:6px;border:1.5px solid #111" role="img" aria-label="Phone screen showing a green-lit car"></div>
    <h2 class="title" style="position:absolute;left:102px;top:32px">Case Studies of<br><i>Overcoming Disruptions</i></h2>
    <div class="point" style="left:114px;top:56px"><span class="badge">A</span><div class="t">Tittle text here</div><p class="fine">Brief note on the first point.</p></div>
    <div class="point" style="left:164px;top:56px"><span class="badge">C</span><div class="t">Tittle text here</div><p class="fine">Brief note on the third point.</p></div>
    <div class="point" style="left:114px;top:79px"><span class="badge">B</span><div class="t">Tittle text here</div><p class="fine">Brief note on the second point.</p></div>
    <div class="point" style="left:164px;top:79px"><span class="badge">D</span><div class="t">Tittle text here</div><p class="fine">Brief note on the fourth point.</p></div>
    <div class="footnote">Insert your footer title here</div>
  </section>

  <section class="slide" style="background:linear-gradient(180deg,var(--paper) 48%,transparent 48%),linear-gradient(90deg,var(--leaf) 52%,var(--paper) 52%)">
    <header class="bar"><span class="brand">VARNOK</span><span class="legal">Copyright © Varnok. All rights reserved</span><span class="dot"></span></header>
    <div class="ph ph-car" style="left:12px;top:26px;width:63px;height:44px" role="img" aria-label="Photo of a green-lit car"></div>
    <div class="ph ph-car2" style="left:84px;top:26px;width:28px;height:84px;background:linear-gradient(180deg,#0b1d10,#2bd14a 45%,#0b1d10)" role="img" aria-label="Photo of green light trails"></div>
    <div class="ph ph-car" style="left:12px;top:76px;width:30px;height:20px" role="img" aria-label="Photo of a car"></div>
    <div class="ph ph-car" style="left:45px;top:76px;width:30px;height:20px" role="img" aria-label="Photo of a car"></div>
    <h2 class="title" style="position:absolute;left:128px;top:40px">Building a Reputation<br>That Attracts Top</h2>
    <p class="fine" style="position:absolute;left:128px;top:58px;width:76px">A short text on how trust grows over time through steady and honest work with every client we serve.</p>
    <p class="fine" style="position:absolute;left:128px;top:77px;width:76px">A second short text on the values that keep people coming back to us.</p>
    <div class="footnote" style="left:98px;width:70px">Insert your footer title here</div>
  </section>

  <section class="slide">
    <header class="bar"><span class="brand">VARNOK</span><span class="legal">Copyright © Varnok. All rights reserved</span><span class="dot"></span></header>
    <h2 class="title" style="position:absolute;left:14px;top:43px">Building a Motivated and<br>Productive Workforce</h2>
    <div style="position:absolute;left:16px;top:82px;width:50px;height:.8px;background:var(--leaf)"></div>
    <div class="ph ph-face" style="left:15px;top:90px;width:14px;height:14px;border-radius:50%" role="img" aria-label="Small round portrait"></div>
    <p class="fine" style="position:absolute;left:35px;top:92px;width:40px;color:var(--ink)">Building a Motivated and Productive Workforce</p>
    <div class="ph ph-car" style="left:120px;top:20px;width:60px;height:59px" role="img" aria-label="Photo of a green-lit car"></div>
    <div class="ph ph-car2" style="left:169px;top:43px;width:36px;height:37px;background:linear-gradient(135deg,#1d5a30,#9fe07a)" role="img" aria-label="Photo of a car under green light"></div>
    <p class="fine" style="position:absolute;left:124px;top:88px;width:80px">A short text on how clear goals and care help a team do its best work.</p>
    <div class="footnote">Insert your footer title here</div>
  </section>

  <section class="slide">
    <header class="bar"><span class="brand">VARNOK</span><span class="legal">Copyright © Varnok. All rights reserved</span><span class="dot"></span></header>
    <h2 class="title" style="position:absolute;top:20px;width:100%;text-align:center">Our Infographic <i>case study</i></h2>
    <div class="ring" style="left:21px;border-color:#8fe0a0"><svg width="10" height="10" viewBox="0 0 10 10" fill="none" stroke="#8fe0a0" stroke-width=".8"><path d="M2 8a6 6 0 0 1 6-6M2 8a3 3 0 0 1 3-3"/><circle cx="2" cy="8" r=".6" fill="#8fe0a0"/></svg></div>
    <div class="ring" style="left:58px;border-color:#0e3a3a"><svg width="10" height="10" viewBox="0 0 10 10" fill="none" stroke="#0e3a3a" stroke-width=".8"><rect x="2" y="2" width="6" height="6"/><rect x="3.7" y="3.7" width="2.6" height="2.6"/></svg></div>
    <div class="ring" style="left:95px;border-color:#141414"><svg width="10" height="10" viewBox="0 0 10 10"><rect x="1" y="3" width="8" height="5.5" rx="1" fill="#141414"/><rect x="3.5" y="2" width="3" height="1.5" fill="#141414"/><circle cx="5" cy="5.7" r="1.5" fill="#fff"/></svg></div>
    <div class="ring" style="left:132px;border-color:#8fe0a0"><svg width="10" height="10" viewBox="0 0 10 10" fill="#8fe0a0"><rect x="2" y="2" width="6" height="1.4"/><rect x="2" y="4.3" width="6" height="1.4"/><rect x="2" y="6.6" width="6" height="1.4"/></svg></div>
    <div class="ring" style="left:169px;border-color:#b8b8b8"><svg width="10" height="10" viewBox="0 0 10 10" fill="none" stroke="#9a9a9a" stroke-width=".8"><rect x="1.5" y="2" width="7" height="4.5"/><path d="M4 8.5h2M5 6.5v2"/></svg></div>
    <div class="step" style="left:18px"><div class="t">Tittle text here</div><p class="fine">A short note on this step.</p></div>
    <div class="step" style="left:55px"><div class="t">Tittle text here</div><p class="fine">A short note on this step.</p></div>
    <div class="step" style="left:92px"><div class="t">Tittle text here</div><p class="fine">A short note on this step.</p></div>
    <div class="step" style="left:129px"><div class="t">Tittle text here</div><p class="fine">A short note on this step.</p></div>
    <div class="step" style="left:166px"><div class="t">Tittle text here</div><p class="fine">A short note on this step.</p></div>
    <div class="footnote">Insert your footer title here</div>
  </section>

  <section class="slide">
    <header class="bar"><span class="brand">VARNOK</span><span class="legal">Copyright © Varnok. All rights reserved</span><span class="dot"></span></header>
    <h2 class="title" style="position:absolute;top:20px;width:100%;text-align:center">Our chart</h2>
    <svg style="position:absolute;left:14px;top:32px" width="186" height="76" viewBox="0 0 186 76">
      <defs><linearGradient id="areaFill" x1="0" y1="0" x2="0" y2="1"><stop offset="0" stop-color="#3c8a5a"/><stop offset="1" stop-color="#e7f6df" stop-opacity=".3"/></linearGradient></defs>
      <g stroke="#f0f2f1" stroke-width=".4"><line x1="6" y1="10" x2="186" y2="10"/><line x1="6" y1="28" x2="186" y2="28"/><line x1="6" y1="46" x2="186" y2="46"/><line x1="6" y1="64" x2="186" y2="64"/></g>
      <path d="M6 70 L40 68 L70 66 L90 60 L100 40 L110 8 L118 20 L124 14 L132 38 L140 50 L150 56 L160 62 L175 66 L186 70 Z" fill="url(#areaFill)"/>
      <polyline points="6,68 20,66 34,69 48,65 62,68 76,64 90,66 104,62 118,67 132,63 146,66 160,64 174,68 186,66" fill="none" stroke="#b7d88f" stroke-width=".5"/>
    </svg>
    <div class="footnote">Insert your footer title here</div>
  </section>

  <section class="slide s-thanks">
    <h2 class="big">VARNOK<br>Thank You</h2>
    <div style="position:absolute;left:108px;top:58px;width:38px;height:.5px;background:#9ab7a7"></div>
    <p class="fine" style="position:absolute;left:152px;top:55px;width:56px;color:#e6efe9">A short closing note and a warm thanks for your time today.</p>
    <div class="contact" style="left:18px"><div class="k">Address</div><div class="v">120 Harbor Lane<br>Oakridge, NV 40210</div></div>
    <div class="contact" style="left:77px"><div class="k">Email</div><div class="v">hello@varnok.example<br>info@varnok.example</div></div>
    <div class="contact" style="left:136px"><div class="k">Phone &amp; Fax</div><div class="v">+0 (555) 010-2244<br>555 010 2299</div></div>
  </section>

</main>
</body>
</html>
```